KVB Website

We need a website for a company based in Doha Qatar called Brightpath Talent Global. It is a global recruitment company, that specializes in both mass recruitment and headhunting. The company is the number 1 one stop shop for recruitment in Qatar. It recruits from all over the world Europe, Asia, Americas, Middle East, Africa for Qatar.

Target Market(s)

Multinational companies, fortune 500 company CEO's, any top earning companies that are looking for a large number of employees or headhunting employees.
Also for candidates looking for companies to work in Qatar.

Industry/Entity Type

Shop

Colors
ffffff

Requirements
Must have
• Most important qualities the website needs to have:
Clean
Modern
Elegant
Professional
Less Tabs
Minimalisitc

Some examples, I would like you to follow are here:
http://www.velmora.ca/
http://www.trovenkip.com/
https://quelbrandix.com/match#

The main color should be white and it has to have a very stylish, modern and cool look. While being minimalistic. I do not want too many tabs. I want it to be simplistic to understand. the only place where the pink logo color is should be in the logo. The logo color should not be anywhere else. It has to be absolutely sleek. Please follow the example websites that I have provided.

I will send the contact details you need to add later. There is no need for a log in page.

Whatever you think that may be important for a recruitment site do suggest. But there is no need for a log in area as we are a different kind of recruitment company.

There should be an area for testimonials from clients. There should also be an area for news flash for the latest countries we are hiring from and the latest companies we are hiring for and the latest positions we are looking for.

Show me the best please. Whoever gives me the best, I will give them an order for the 2nd website too.

Nice to have
• I have included a powerpoint to explain more!

```html
<!DOCTYPE html>
<html lang="en">
<head>
<meta charset="utf-8">
<title>Brightpath Talent Global — Work</title>
<link href="https://fonts.googleapis.com/css2?family=Zilla+Slab:ital,wght@0,400;0,500;0,600;1,300&display=swap" rel="stylesheet">
<style>
  :root {
    --page-bg: #f6f6f6;
    --header-bg: #ffffff;
    --card-bg: #efefef;
    --text-strong: #555555;
    --text-body: #6a6a6a;
    --text-muted: #7a7a7a;
    --nav-text: #4a4a4a;
    --nav-active: #5e5e5e;
    --brand-pink: #a3195b;
    --client-navy: #13294b;
    --rule: #9aa3b0;
    --flag-saffron: #ff9933;
    --flag-green: #138808;
    --flag-navy: #012169;
    --flag-red: #c8102e;
    --flag-pl-red: #dc143c;
    --white: #ffffff;
  }
  * { margin: 0; padding: 0; box-sizing: border-box; }
  html, body { width: 1200px; height: 900px; overflow: hidden; }
  body {
    position: relative;
    font-family: "Zilla Slab", Georgia, serif;
    background: linear-gradient(180deg, #ececec 0px, var(--page-bg) 120px, var(--page-bg) 100%);
    color: var(--text-body);
  }
  .site-header {
    position: absolute; left: 0; top: 0; width: 1200px; height: 92px;
    background: var(--header-bg);
    box-shadow: 0 6px 14px rgba(0,0,0,0.06);
  }
  .brand {
    position: absolute; left: 108px; top: 30px;
    display: flex; align-items: center; gap: 10px;
    color: var(--brand-pink); font-weight: 600; font-size: 24px; letter-spacing: 0.2px;
  }
  .brand-mark { width: 14px; height: 14px; border-radius: 50%; background: var(--brand-pink); }
  .main-nav { position: absolute; top: 0; left: 0; width: 100%; height: 92px; }
  .nav-link {
    position: absolute; top: 50px; font-size: 19px; font-weight: 500;
    color: var(--nav-text); text-decoration: none;
  }
  .nav-link.is-active::after {
    content: ""; position: absolute; left: 0; right: 0; top: 32px; height: 7px;
    background: var(--nav-active);
  }
  .page-intro {
    position: absolute; left: 0; width: 1200px; top: 162px; text-align: center;
    font-size: 33px; font-weight: 400; color: var(--text-muted);
  }
  .card { position: absolute; background: var(--card-bg); }
  .client-card { left: 108px; top: 250px; width: 257px; height: 127px; }
  .client-name-block {
    position: absolute; left: 15px; top: 13px; width: 225px; height: 70px;
    display: flex; align-items: center; justify-content: center;
    color: var(--client-navy); font-size: 22px; font-weight: 500; letter-spacing: 2px;
  }
  .client-label {
    position: absolute; left: 0; width: 100%; top: 94px; text-align: center;
    font-size: 17px; font-weight: 600; color: var(--text-strong);
  }
  .project-card { left: 397px; top: 250px; width: 674px; height: 127px; }
  .project-title {
    position: absolute; left: 21px; top: 10px; font-size: 23px;
    font-style: italic; font-weight: 300; color: var(--text-muted);
  }
  .project-text {
    position: absolute; left: 21px; top: 40px; width: 590px;
    font-size: 12.5px; line-height: 16.8px; color: var(--text-body);
  }
  .hiring-card { left: 397px; top: 405px; width: 674px; height: 333px; }
  .hiring-head {
    position: absolute; top: 13px; font-size: 15.5px; letter-spacing: 0.4px;
    color: var(--text-strong);
  }
  .hiring-head.from { left: 29px; }
  .hiring-head.position { left: 265px; }
  .hiring-head.count { left: 457px; }
  .head-rule {
    position: absolute; left: 29px; width: 618px; top: 33px;
    border-top: 1px dashed var(--rule);
  }
  .country-row { position: absolute; left: 0; width: 100%; }
  .flag { position: absolute; left: 42px; top: 0; width: 89px; height: 57px; display: block; }
  .role-list {
    position: absolute; left: 252px; top: 0; padding-left: 6px;
    border-left: 1px dashed #8a8a8a; list-style: none;
  }
  .role-list li { font-size: 13px; line-height: 24px; color: var(--text-body); }
  .count-list { position: absolute; left: 542px; top: 0; list-style: none; }
  .count-list li { font-size: 13px; line-height: 24px; color: var(--text-body); }
</style>
</head>
<body>
  <header class="site-header">
    <div class="brand"><span class="brand-mark"></span>Brightpath Talent Global</div>
    <nav class="main-nav">
      <a class="nav-link" href="#" style="left:793px">Home</a>
      <a class="nav-link is-active" href="#" style="left:899px">Work</a>
      <a class="nav-link" href="#" style="left:993px">Contact</a>
    </nav>
  </header>

  <h1 class="page-intro">Below you can find job openings for the latest projects.</h1>

  <section class="card client-card">
    <div class="client-name-block">GRAND LARKMERE</div>
    <p class="client-label">Grand Larkmere Hotels</p>
  </section>

  <section class="card project-card">
    <h2 class="project-title">Project</h2>
    <p class="project-text">Lorem ipsum dolor sit amet, consectetur adipiscing elit. Nullam lacinia bibendum ante, vitae blandit dolor faucibus ut. Etiam molestie pellentesque tortor, sed scelerisque massa dignissim et. Phasellus aliquet eget sem at ornare. Cras aliquam fermentum enim, sit amet lacinia nibh eleifend ac. Vivamus laoreet, sapien id vestibulum lacinia, augue sem molestie leo, ut lacinia mi enim in nibh.</p>
  </section>

  <section class="card hiring-card">
    <span class="hiring-head from">HIRING FROM</span>
    <span class="hiring-head position">POSITION</span>
    <span class="hiring-head count">NUMBER OF WORKERS</span>
    <div class="head-rule"></div>

    <div class="country-row" style="top:57px">
      <svg class="flag" viewBox="0 0 89 57" role="img" aria-label="Flag of India">
        <rect width="89" height="19" fill="var(--flag-saffron)"/>
        <rect y="19" width="89" height="19" fill="var(--white)"/>
        <rect y="38" width="89" height="19" fill="var(--flag-green)"/>
        <circle cx="44.5" cy="28.5" r="7" fill="none" stroke="var(--flag-navy)" stroke-width="1.5"/>
        <circle cx="44.5" cy="28.5" r="1.6" fill="var(--flag-navy)"/>
      </svg>
      <ul class="role-list"><li>Construction worker</li><li>Construction supervisor</li><li>Cleaning personel</li></ul>
      <ul class="count-list"><li>120</li><li>6</li><li>20</li></ul>
    </div>

    <div class="country-row" style="top:158px">
      <svg class="flag" viewBox="0 0 89 53" role="img" aria-label="Flag of the United Kingdom">
        <rect width="89" height="53" fill="var(--flag-navy)"/>
        <path d="M0 0 L89 53 M89 0 L0 53" stroke="var(--white)" stroke-width="10"/>
        <path d="M0 0 L89 53 M89 0 L0 53" stroke="var(--flag-red)" stroke-width="3.5"/>
        <path d="M44.5 0 V53 M0 26.5 H89" stroke="var(--white)" stroke-width="16"/>
        <path d="M44.5 0 V53 M0 26.5 H89" stroke="var(--flag-red)" stroke-width="9"/>
      </svg>
      <ul class="role-list"><li>Senior planning manager</li><li>Senior development manager</li></ul>
      <ul class="count-list"><li>4</li><li>5</li></ul>
    </div>

    <div class="country-row" style="top:252px">
      <svg class="flag" viewBox="0 0 89 54" role="img" aria-label="Flag of Poland">
        <rect width="89" height="27" fill="var(--white)"/>
        <rect y="27" width="89" height="27" fill="var(--flag-pl-red)"/>
      </svg>
      <ul class="role-list"><li>Construction engineer</li><li>Civil engineer</li></ul>
      <ul class="count-list"><li>12</li><li>24</li></ul>
    </div>
  </section>
</body>
</html>
```